Residential & commercial landscaping company

Updated business cards for commercial and landscaping company. We would like to keep out logo, but just need a more updated business card.

```html
<!DOCTYPE html>
<html lang="en">
<head>
<meta charset="utf-8">
<title>Greenfield – Business Cards</title>
<link href="https://fonts.googleapis.com/css2?family=Arimo:wght@400;700&family=Tinos:wght@700&display=swap" rel="stylesheet">
<style>
  :root {
    --bg: #2b2b2b;
    --green-light: #52bf4a;
    --green-mid: #0a9c39;
    --green-deep: #066e33;
    --green-text: #2ec43a;
    --ink: #141414;
    --paper: #ffffff;
  }
  html, body {
    margin: 0;
    width: 1200px;
    height: 1015px;
    overflow: hidden;
    background: radial-gradient(ellipse at center, #3a3a3a 0%, var(--bg) 60%, #161616 100%);
  }
  .sheet {
    position: relative;
    width: 1200px;
    height: 1015px;
  }
  .card {
    position: absolute;
    top: 353px;
    width: 540px;
    height: 309px;
    overflow: hidden;
    box-shadow: 0 12px 30px rgba(0,0,0,.55);
  }
  .card--front {
    left: 30px;
    background: linear-gradient(160deg, var(--green-light) 0%, var(--green-mid) 45%, var(--green-deep) 100%);
  }
  .card--back {
    left: 630px;
    background: var(--paper);
  }
  .wordmark {
    position: absolute;
    display: flex;
    align-items: center;
    gap: 12px;
    font-family: "Arimo", Arial, sans-serif;
    font-weight: 700;
    letter-spacing: -1px;
  }
  .card--front .wordmark {
    left: 0; right: 0; top: 118px;
    justify-content: center;
    font-size: 60px;
    color: var(--paper);
  }
  .wordmark__square {
    width: 34px; height: 34px;
    background: currentColor;
  }
  .card--back .stripes {
    position: absolute;
    left: 0; top: 0;
  }
  .card--back .wordmark {
    left: 150px; top: 92px;
    font-size: 50px;
    color: var(--ink);
  }
  .card--back .wordmark__square {
    width: 28px; height: 28px;
    background: var(--green-mid);
  }
  .contact-band {
    position: absolute;
    left: 0; right: 0; bottom: 0;
    height: 96px;
    background: var(--ink);
  }
  .contact {
    position: absolute;
    left: 150px; top: 172px;
    font-family: "Arimo", Arial, sans-serif;
    font-size: 14px;
    color: #f2f2f2;
    line-height: 1.45;
  }
  .contact__name {
    font-family: "Tinos", "Times New Roman", serif;
    font-weight: 700;
    font-size: 21px;
    color: var(--green-text);
    margin: 0 0 18px;
  }
  .contact__role { font-weight: 400; }
  .contact__line { margin: 0; }
  .contact__label {
    font-weight: 700;
    color: var(--green-text);
  }
</style>
</head>
<body>
<main class="sheet">
  <section class="card card--front" aria-label="Business card front">
    <div class="wordmark"><span class="wordmark__square"></span>Greenfield</div>
  </section>

  <section class="card card--back" aria-label="Business card back">
    <svg class="stripes" width="540" height="309" viewBox="0 0 540 309" aria-hidden="true">
      <rect x="0" y="0" width="540" height="13" fill="var(--green-light)"/>
      <rect x="0" y="15" width="540" height="13" fill="var(--green-mid)"/>
      <rect x="0" y="30" width="540" height="13" fill="var(--green-deep)"/>
      <polygon points="120,46 185,2 290,46" fill="var(--paper)"/>
    </svg>
    <div class="wordmark"><span class="wordmark__square"></span>Greenfield</div>
    <div class="contact-band"></div>
    <div class="contact">
      <p class="contact__name">Daniel Hartwell Jr. <span class="contact__role">- Project Manager</span></p>
      <p class="contact__line">555-201-0250 ext.412 | <span class="contact__label">Fax:</span> 555-310-1271</p>
      <p class="contact__line"><span class="contact__label">Email:</span> dan@GreenfieldLandscapes.com</p>
    </div>
  </section>
</main>
</body>
</html>
```